Business Card Design

We need a design for business cards for our company. We have a logo. We teach EMT's and we are based out of Virginia. The information that will need to add would be, name, title, phone number, email, address. On the back of the business card would be "We help you, help others"

Target Market(s)

People that want to become EMT's

Colors

Designer to choose colors to be used in the design.

Requirements
Must have
• company logo

```html
<!DOCTYPE html>
<html lang="en">
<head>
<meta charset="utf-8">
<title>Crestpoint Rescue Academy – Business Cards</title>
<link rel="stylesheet" href="https://fonts.googleapis.com/css2?family=Rubik:wght@400;500&display=swap">
<style>
  :root {
    --brand-red: #c01f2f;
    --brand-red-deep: #b31a2a;
    --ink-grey: #8a8a8a;
    --rule-grey: #b5b5b5;
    --paper: #ffffff;
    --backdrop: #e9e7e4;
  }
  * { box-sizing: border-box; margin: 0; padding: 0; }
  html, body { width: 1200px; height: 912px; overflow: hidden; }
  body {
    background: var(--backdrop);
    font-family: "Rubik", sans-serif;
    position: relative;
  }
  .card {
    position: absolute;
    width: 560px;
    height: 320px;
    box-shadow: 0 14px 30px rgba(0,0,0,0.22);
    overflow: hidden;
  }
  /* Back of card */
  .card-back {
    left: 70px; top: 70px;
    background: var(--brand-red);
  }
  .card-back .pattern-field {
    position: absolute; inset: 0;
    background: linear-gradient(135deg, var(--brand-red) 0%, var(--brand-red-deep) 100%);
  }
  .card-back .wordmark {
    position: absolute;
    left: 0; right: 0; top: 142px;
    text-align: center;
    color: var(--paper);
    font-weight: 500;
    font-size: 28px;
    letter-spacing: 0.5px;
  }
  /* Front of card */
  .card-front {
    left: 570px; top: 500px;
    background: var(--paper);
  }
  .card-front .wordmark {
    position: absolute;
    right: 34px; top: 38px;
    color: var(--brand-red);
    font-weight: 500;
    font-size: 20px;
    letter-spacing: 0.3px;
  }
  .card-front .divider {
    position: absolute;
    left: 150px; right: 30px; top: 96px;
    height: 1.5px;
    background: var(--brand-red);
  }
  .card-front .name-marker {
    position: absolute;
    left: 0; top: 140px;
    width: 10px; height: 40px;
    background: var(--brand-red);
  }
  .card-front .person {
    position: absolute;
    left: 32px; top: 134px;
  }
  .person .name {
    color: var(--brand-red);
    font-weight: 500;
    font-size: 24px;
    letter-spacing: 0.5px;
    text-transform: uppercase;
  }
  .person .title {
    color: var(--ink-grey);
    font-size: 15px;
    margin-top: 2px;
  }
  .card-front .contact-rule {
    position: absolute;
    left: 32px; top: 200px;
    width: 260px; height: 1.5px;
    background: var(--brand-red);
  }
  .contact-list {
    position: absolute;
    left: 32px; top: 212px;
    list-style: none;
    color: var(--ink-grey);
    font-size: 14px;
    line-height: 21px;
  }
  .contact-list li { display: flex; align-items: center; gap: 8px; }
  .contact-list svg { width: 11px; height: 11px; flex: none; }
  .contact-list .web-accent { color: var(--brand-red); }
  .address {
    position: absolute;
    right: 30px; top: 182px;
    text-align: right;
    color: var(--ink-grey);
    font-size: 13px;
    line-height: 19px;
  }
  .base-band {
    position: absolute; left: 0; top: 0;
    width: 560px; height: 320px;
  }
</style>
</head>
<body>

  <section class="card card-back" aria-label="Back of business card">
    <div class="pattern-field" role="img" aria-label="Red background with a faint repeating pattern of medical crosses"></div>
    <div class="wordmark">Crestpoint Rescue Academy</div>
  </section>

  <section class="card card-front" aria-label="Front of business card">
    <svg class="base-band" viewBox="0 0 560 320" aria-hidden="true">
      <path d="M0 296 L368 296 C398 296 405 256 440 254 L560 254" fill="none" stroke="var(--rule-grey)" stroke-width="5"/>
      <path d="M0 306 L380 306 C412 306 418 264 452 262 L560 262 L560 320 L0 320 Z" fill="var(--brand-red)"/>
    </svg>

    <div class="wordmark">Crestpoint Rescue Academy</div>
    <div class="divider"></div>

    <div class="name-marker"></div>
    <div class="person">
      <div class="name">Dana Whitlow</div>
      <div class="title">Director</div>
    </div>
    <div class="contact-rule"></div>

    <ul class="contact-list">
      <li>
        <svg viewBox="0 0 12 12"><path d="M3 1 L5 3.5 L4 5 C4.8 6.6 5.6 7.4 7 8 L8.5 7 L11 9 L9.5 11 C5 10.5 1.5 7 1 2.5 Z" fill="var(--brand-red)"/></svg>
        555-014-2290
      </li>
      <li>
        <svg viewBox="0 0 12 12"><rect x="1" y="2.5" width="10" height="7" fill="none" stroke="var(--brand-red)" stroke-width="1.2"/><path d="M1 2.5 L6 6.5 L11 2.5" fill="none" stroke="var(--brand-red)" stroke-width="1.2"/></svg>
        hello@crestpointrescue.com
      </li>
      <li>
        <svg viewBox="0 0 12 12"><circle cx="6" cy="6" r="5" fill="var(--brand-red)"/><path d="M1 6 H11 M6 1 C3.5 4 3.5 8 6 11 M6 1 C8.5 4 8.5 8 6 11" fill="none" stroke="#fff" stroke-width="0.8"/></svg>
        <span>www.<span class="web-accent">crestpointrescue</span>.com</span>
      </li>
    </ul>

    <address class="address" style="font-style:normal">
      418 Harbor Lane<br>
      Millbrook, VA 23101
    </address>
  </section>

</body>
</html>
```